Contemporary Business card for Event Manager

Needed for my startup events company in Melbourne. Events I manage will be based within the fashion industry, sporting events, product launches etc. Not weddings or small dinner parties. Therfore I am after something professional and aimed at high end corporate market; but with the added emphasis on not being too conservative or boring. I am happy with a pop of colour e.g. yellow or copper foil.

Target Market(s)

fashion industry, design industry, high end sporting events e.g. Polo, Grand Prix, corporate clients,

Industry/Entity Type

Fashion

Contact Information for Business Card

side 1
Lucy Brandt (can be upper or lower case, have a feature full stop between first and surname, or at the end of the nameetc) I am open to ideas. I would also be fine with my initials or name as a logo on the front (if this is the case my full name would need to go on the second side of the card.
2nd side:
Mobile: +61 400 817 263
email: lucy.brandt@mailnest.com.au

on one side of the card:
event management | brand activation | Advisory Services

Font styles to use
Serif
Sans Serif

Requirements
Must have
• side 2 must have
• mobile number
• email address
• event management | brand activation | Advisory Services
• ** my full name (Lucy Brandt) must be on the card somewhere)
Nice to have
• 1st side
• I see the card stock being either a dark grey, light grey, natural white or black (all matt colours on unprocessed card). I see the writing being copper foil, or foil white or foil black.
• To give you a feel for me, think: contemporary, minimalist, I love line drawings, concrete, white with grey vein marble, copper, white, grey, black...yes I do like colour....yellow (but pops of colour) ;) I would like the card to look designer but 'on trend' as I deal with a lot of design and fashion clients....styles - think the sophistication and simplicity of Vireaux or urban contemporary.
• some examples of what I like. Although please don't leet this limit you...I really am happy to have something a little more urban or design focused like a line drawing of an object, person too or a photo image too.
• https://www.moodtackle.com/pin/830165427719302846/
• https://www.moodtackle.com/pin/607281935540173268/
• https://www.moodtackle.com/pin/318746205913457092/
• https://www.moodtackle.com/pin/41983627530918476/
• https://www.moodtackle.com/pin/53128940672419087/
• https://www.moodtackle.com/pin/90316284750638152/
• https://www.moodtackle.com/pin/734092618450362918/
• https://www.moodtackle.com/pin/926354081736215407/
• https://www.moodtackle.com/pin/481627093518704356/
Should not have
• should not look commercial or have cartoonish looking logos. However happy with a simple line drawing or logo with initials etc.

```html
<!DOCTYPE html>
<html lang="en">
<head>
<meta charset="utf-8">
<title>Lucy Brandt — Business Card</title>
<link rel="stylesheet" href="https://fonts.googleapis.com/css2?family=Tinos:wght@400&display=swap">
<style>
  :root {
    --backdrop: #e6e4e4;
    --card-dark: #1d1d1d;
    --card-mid: #2c2c2c;
    --card-light: #363636;
    --foil-yellow: #f5ef10;
  }
  * { margin: 0; padding: 0; box-sizing: border-box; }
  html, body {
    width: 1200px;
    height: 862px;
    overflow: hidden;
    background: var(--backdrop);
  }
  .canvas {
    position: relative;
    width: 1200px;
    height: 862px;
    display: flex;
    justify-content: center;
    align-items: center;
    gap: 80px;
  }
  .card {
    position: relative;
    width: 380px;
    height: 620px;
    overflow: hidden;
    box-shadow: 0 8px 24px rgba(0,0,0,0.25);
    font-family: "Tinos", "Times New Roman", serif;
    color: var(--foil-yellow);
  }
  .card-texture {
    position: absolute;
    inset: 0;
    background: linear-gradient(90deg,
      var(--card-dark) 0%, var(--card-mid) 18%, var(--card-dark) 34%,
      var(--card-light) 52%, var(--card-dark) 70%, var(--card-mid) 86%, var(--card-dark) 100%);
  }
  .card-content {
    position: absolute;
    inset: 0;
    display: flex;
    flex-direction: column;
    align-items: center;
    text-align: center;
  }
  .card--front .card-content { justify-content: center; padding-bottom: 60px; }
  .holder-name {
    font-size: 44px;
    font-weight: 400;
    letter-spacing: 0.5px;
  }
  .card--back .card-content { padding-top: 218px; }
  .contact-phone {
    font-size: 44px;
    letter-spacing: 1px;
  }
  .contact-email {
    margin-top: 28px;
    font-size: 27px;
  }
  .service-list {
    list-style: none;
    margin-top: 58px;
    font-size: 29px;
    line-height: 1.3;
  }
</style>
</head>
<body>
  <main class="canvas">
    <section class="card card--front">
      <div class="card-texture" role="img" aria-label="Dark charcoal wood grain card stock"></div>
      <div class="card-content">
        <h1 class="holder-name">Lucy Brandt.</h1>
      </div>
    </section>
    <section class="card card--back">
      <div class="card-texture" role="img" aria-label="Dark charcoal wood grain card stock"></div>
      <div class="card-content">
        <p class="contact-phone">61 400 817 263</p>
        <p class="contact-email">lucy.brandt@mailnest.com.au</p>
        <ul class="service-list">
          <li>event management</li>
          <li>brand activation</li>
          <li>Advisory Services</li>
        </ul>
      </div>
    </section>
  </main>
</body>
</html>
```